Website development company website

ABOUT COMPANY
Hi everyone! We're a Melbourne, Australia website development company in a need of a website design that will make online store merchants want to engage our services.
We specialise exclusively in Torvista e-commerce platform (https://torvista-platform.example/). What distinguishes our business from competition is that rather than designing and building brand new websites, we offer development, support and maintenance services to established websites. Maintenance and Support are the keywords representing our business.
Our potential clients are people with broken, slow and underperforming Torvista installations who need assistance getting their websites up and making sales. Our website must pass the message that we can help, and provide quick means of making contact.
DESIGN
Overall, we're looking for a slick, clean, airy, conservative design. No need to do anything crazy, try to stick to what's "standard" in website design these days and make it easy on all of us. The website is unlikely to be updated too often so it needs to look attractive and fresh first time over and after a year, too.
Attached is our new logo, which you'll be able to take the basic idea from, the colors and fonts. Though, don't use the fonts from the logo in the website, stick to the standard widely supported fonts. Additional use of Google fonts is fine.
Don't overdo it with colors, stick to conservative basic color set and only use the colors from the log for accents like headings etc. Please, don't be tempted to use the blue and orange as background of whole blocks, other than perhaps footer. Thanks.
For the images used, I'd like to stay away from a design studio/digital agency feel and lean more towards professional support and maintenance services. I'm thinking images of content merchants doing their job. Something along the lines of "We'll be taking care of the website so that you only need to care about the business".
Some ideas I like:
http://www.plumframe-pics.example/detail/photo/portrait-of-confident-male-design-professional-royalty-free-image/572048163
http://www.plumframe-pics.example/detail/photo/designer-taking-picture-of-hat-high-res-stock-photography/839207514
http://www.plumframe-pics.example/detail/photo/woman-packaging-pottery-royalty-free-image/216684093
Images of colorful shopping bags and shopping carts are over the top and not serious enough. Instead of images matching Online Shopping, I'd try going more for Stability, Reliability, Performance.
Our existing website is http://www.bravuln.example. Please, don't take design ideas from it, but it will give you a picture of the structure of our new website and content that's going to be used initially.
If you could include a basic icon set to use throughout the website, that would be great. If the icons could match our logo (attached), it would be a big plus.
ALL PAGES
Every page must contain clearly visible phone number (1300 648 907) and a Contact Us Now button, which opens an AJAX driven popup form with Name, Email, Phone and Message to be sent through.
To start with, main menu items will be Torvista, Portfolio, Contact.
At the bottom of each page, please, include a newsletter subscription form with text Subscribe to Torvista Support and Security Updates.
For the footer, I'd like to see a logo strip with the following logos in grayscale (no need to link anywhere): Torvista, QRX, DataVane, NCB. You'll find the logos on Google Images.
Standard footer columns follow. Here, I'd like to see logos in color: Torvista Certified Developer, Torvista Ceritified Solution Provider. Again, the logos are on Google Images.
No social media logos/links necessary anywhere on the website.
...and then the copyright line.
FRONT PAGE
Large slider with images that would appeal to our target audience. Keywords here would be Torvista System Audit, Torvista Performance Optimisation, Torvista Website Emergency Recovery, Torvista Development Infrastructure Hosting. We'll have a static page created for each of these to link to.
In a corner of the slider, or on the edge, can I have an overlay with logos in color (same as footer): Torvista Certified Developer, Torvista Ceritified Solution Provider.
Underneath, a number of blocks, each with an image and teaser that we'll use to link to various pages throughout the website.
PORTFOLIO PAGE
I'm thinking a single long page with a block per client, which will contain project name, description from us and a testimonial from client. Also, each block will contain a single large screenshot. No gallery or slideshow is necessary here, just one image per project.
I'll leave the layout up to you, but try to put yourself in the shoes of a potential client reviewing our past work by simply scrolling down this one page.
CONTACT US PAGE
Separate page with the same form as above, phone number (1300 648 907), email address (support@kavreo.example), address (Suite 42, Level 3|8 Wattlebrook Lane|Fernvale Heights VIC 3999), and a grayscale Google Map.
CODING UP
Coding up into static HTML/CSS/JS is equally important as the design itself. We're a website development company, we'll be integrating the theme. We will spot any issues and we will point them out.
Coded up design must be fully responsive. Enough said.
To be able to create any content in future, we'd like one extra page coded up with samples of all themed elements, lists, forms, buttons, 2, 3, 4-column layout, alerts, icons, etc. This page does not need to be designed, only coded up.
The design will be integrated into Drupal using Twig. If possible at all, try to keep it in mind when designing and coding up, and make the integration into a Drupal theme easier for us.
GOOD LUCK!
That's it. Let me know if anything needs clarifying. So far I've had a great experience with ArtFlockly. I don't doubt some great designs will emerge. Clever ideas are highly appreciated, but also make it clear you've read and followed the points in this brief. Cheers, Tom

```html
<!DOCTYPE html>
<html lang="en">
<head>
<meta charset="utf-8">
<title>Kavreo – Torvista Development, Support &amp; Maintenance</title>
<link rel="stylesheet" href="https://fonts.googleapis.com/css2?family=Raleway:wght@300;400;700;800&family=Open+Sans:wght@400;600;700&family=Lato:wght@400;700&display=swap">
<style>
  :root {
    --navy: #0e3a6c;
    --navy-dark: #0b3564;
    --footer-blue: #0d4482;
    --orange: #e67e22;
    --grey-text: #6b6b6b;
    --nav-text: #5a5a5a;
    --box-border: #dcdcdc;
    --white: #ffffff;
  }
  * { box-sizing: border-box; margin: 0; padding: 0; }
  html, body { width: 714px; height: 1200px; overflow: hidden; background: var(--white); }
  body { font-family: "Open Sans", Arial, sans-serif; position: relative; }

  /* Hero */
  .hero { position: absolute; left: 0; top: 0; width: 714px; height: 434px; }
  .hero-photo {
    position: absolute; inset: 0;
    background: linear-gradient(180deg, #e4eaf0 0%, #d6dde4 45%, #e9ecef 80%, #f3f3f3 100%);
  }
  .brand { position: absolute; left: 46px; top: 14px; display: flex; align-items: center; gap: 7px; }
  .brand-mark { width: 24px; height: 24px; background: var(--navy); border-radius: 3px; }
  .brand-name { font-family: "Raleway", sans-serif; font-weight: 800; font-size: 24px; color: var(--navy); }
  .main-nav { position: absolute; top: 24px; left: 373px; display: flex; }
  .main-nav a {
    font-family: "Raleway", sans-serif; font-size: 10.5px; color: var(--nav-text);
    text-decoration: none; margin-right: 29px; letter-spacing: .2px;
  }
  .main-nav a.active { color: var(--navy); }
  .main-nav a:last-child { margin-right: 0; }
  .hero-title {
    position: absolute; left: 0; width: 714px; top: 208px; text-align: center;
    font-family: "Raleway", sans-serif; font-weight: 800; font-size: 25.5px; line-height: 32px;
    color: var(--navy);
  }
  .btn-contact {
    position: absolute; left: 290px; top: 281px; width: 134px; height: 35px;
    background: var(--navy-dark); color: var(--white); font-family: "Raleway", sans-serif;
    font-weight: 700; font-size: 13.5px; display: flex; align-items: center; justify-content: center;
    text-decoration: none;
  }

  /* Services */
  .services { position: absolute; top: 434px; left: 0; width: 714px; height: 246px; }
  .section-title {
    font-family: "Raleway", sans-serif; font-weight: 300; font-size: 26px; text-align: center;
    color: var(--navy); letter-spacing: .3px;
  }
  .services .section-title { margin-top: 30px; }
  .service-grid {
    position: absolute; left: 81px; top: 72px; width: 555px; height: 142px;
    display: flex; border: 1px solid var(--box-border);
  }
  .service-card {
    flex: 1; text-align: center; border-right: 1px solid var(--box-border);
    background: linear-gradient(180deg, #fdfdfd 0%, #ededed 100%);
    padding-top: 22px;
  }
  .service-card:last-child { border-right: none; }
  .service-icon { width: 50px; height: 36px; display: block; margin: 0 auto; }
  .service-name {
    font-family: "Raleway", sans-serif; font-weight: 400; font-size: 11.5px; color: var(--navy);
    margin-top: 7px; letter-spacing: .2px;
  }
  .service-text { font-size: 9.5px; line-height: 15px; color: var(--grey-text); margin-top: 3px; }

  /* Partners */
  .partners { position: absolute; top: 680px; left: 0; width: 714px; height: 220px; }
  .partners-photo {
    position: absolute; inset: 0;
    background: linear-gradient(90deg, #e8dccb 0%, #f2ece4 30%, #f6f2ee 55%, #eee2d6 80%, #e6d8c8 100%);
  }
  .partners .section-title { position: absolute; top: 28px; width: 100%; color: #111; }
  .slider-arrow { position: absolute; top: 99px; width: 25px; height: 25px; }
  .slider-arrow.prev { left: 46px; }
  .slider-arrow.next { left: 643px; }
  .partner-logo {
    position: absolute; top: 122px; left: 0; width: 714px; display: flex; align-items: center;
    justify-content: center; gap: 7px;
  }
  .partner-logo-mark { width: 16px; height: 16px; border-radius: 50%; background: #1f5fae; }
  .partner-logo-name { font-family: "Open Sans", sans-serif; font-weight: 700; font-size: 16px; color: #111; }
  .testimonial {
    position: absolute; top: 152px; left: 170px; width: 374px; text-align: center;
    font-size: 9.2px; line-height: 17px; color: #111;
  }

  /* Newsletter */
  .newsletter {
    position: absolute; top: 900px; left: 0; width: 714px; height: 89px; background: var(--navy-dark);
  }
  .newsletter-icon { position: absolute; left: 47px; top: 32px; }
  .newsletter-label {
    position: absolute; left: 89px; top: 36px; font-family: "Lato", sans-serif; font-size: 12.5px;
    color: var(--white);
  }
  .newsletter-form { position: absolute; left: 296px; top: 31px; display: flex; }
  .newsletter-input {
    width: 248px; height: 27px; border: none; padding-left: 10px;
    font-family: "Lato", sans-serif; font-size: 11.5px; color: #999; background: var(--white);
  }
  .newsletter-button {
    width: 111px; height: 27px; border: none; background: var(--orange); color: var(--white);
    font-family: "Lato", sans-serif; font-size: 12px; letter-spacing: .4px;
  }

  /* Footer */
  .site-footer {
    position: absolute; top: 989px; left: 0; width: 714px; height: 211px; background: var(--footer-blue);
    color: var(--white);
  }
  .footer-heading {
    position: absolute; top: 36px; font-family: "Lato", sans-serif; font-weight: 400;
    font-size: 11.5px; letter-spacing: .3px;
  }
  .footer-heading.links { left: 49px; }
  .footer-heading.contact { left: 252px; }
  .footer-heading.partners-title { left: 514px; }
  .footer-links { position: absolute; left: 49px; top: 59px; list-style: none; }
  .footer-links li { font-size: 9.5px; line-height: 18.2px; }
  .contact-list { position: absolute; left: 250px; top: 60px; list-style: none; }
  .contact-list li { display: flex; align-items: flex-start; gap: 12px; font-size: 9px; line-height: 15px; margin-bottom: 11px; }
  .contact-list svg { flex: none; margin-top: 2px; }
  .partner-badges {
    position: absolute; left: 514px; top: 62px; display: grid;
    grid-template-columns: 84px 84px; row-gap: 22px;
  }
  .partner-badge {
    display: flex; align-items: center; gap: 5px; height: 30px;
    font-family: "Open Sans", sans-serif; font-weight: 600; font-size: 11px;
  }
  .partner-badge-mark { width: 10px; height: 10px; background: var(--white); flex: none; }
  .copyright { position: absolute; bottom: 19px; width: 100%; text-align: center; font-size: 9.3px; }
  .copyright strong { font-weight: 700; }
</style>
</head>
<body>

<header class="hero">
  <div class="hero-photo" role="img" aria-label="Two smiling colleagues working together at a laptop in a bright office"></div>
  <div class="brand">
    <span class="brand-mark"></span>
    <span class="brand-name">Kavreo</span>
  </div>
  <nav class="main-nav">
    <a class="active" href="#">HOME</a>
    <a href="#">ABOUT US</a>
    <a href="#">PORTFOLIO</a>
    <a href="#">CONTACT US</a>
  </nav>
  <h1 class="hero-title">HIGHT PERFORMANCE TORVISTA SITES<br>ON TIME AND ON BUDGET</h1>
  <a class="btn-contact" href="#">Contact Us</a>
</header>

<section class="services">
  <h2 class="section-title">SERVICES</h2>
  <div class="service-grid">
    <article class="service-card">
      <svg class="service-icon" viewBox="0 0 50 36" fill="none" stroke="#e67e22" stroke-width="3">
        <rect x="10" y="4" width="30" height="21" rx="1.5"/>
        <path d="M3 30 h44 v2 h-44 z" fill="#e67e22" stroke-linejoin="round"/>
      </svg>
      <h3 class="service-name">DEVLOPMENT</h3>
      <p class="service-text">We offer development, support and<br>maintenance services to&nbsp; websites.</p>
    </article>
    <article class="service-card">
      <svg class="service-icon" viewBox="0 0 50 36">
        <rect x="3" y="9" width="7" height="19" fill="#e67e22"/>
        <rect x="40" y="9" width="7" height="19" fill="#e67e22"/>
        <path d="M12 11 l9 -2 l8 3 l-7 4 a3 3 0 0 0 4 3 l5 -2 l7 7 l-4 4 l-3 0 l-3 3 l-4 -1 l-3 1 l-9 -6 z" fill="#e67e22"/>
        <path d="M29 12 l9 -1 v14 l-3 1" fill="none" stroke="#e67e22" stroke-width="2.5"/>
      </svg>
      <h3 class="service-name">SUPPORT</h3>
      <p class="service-text">We offer development, support and<br>maintenance services to&nbsp; websites.</p>
    </article>
    <article class="service-card">
      <svg class="service-icon" viewBox="0 0 50 36" fill="none" stroke="#e67e22" stroke-width="2.4" stroke-linecap="round" stroke-linejoin="round">
        <path d="M14 3 a6 6 0 0 0 2 9 l17 20 a2.5 2.5 0 0 0 4 -3 l-19 -18 a6 6 0 0 0 -8 -6 l4 4 l-1 3 l-3 1 l-4 -4"/>
        <path d="M36 3 l5 3 l-3 4 l-3 0 l-19 19 l-2 4 l-3 1 l-1 -1 l1 -3 l4 -2 l19 -19 z"/>
      </svg>
      <h3 class="service-name">MAINTENANCE</h3>
      <p class="service-text">We offer development, support and<br>maintenance services to&nbsp; websites.</p>
    </article>
  </div>
</section>

<section class="partners">
  <div class="partners-photo" role="img" aria-label="Smiling woman resting her chin on her hand beside design swatches and paint tins"></div>
  <h2 class="section-title">OUR PARTNERS</h2>
  <svg class="slider-arrow prev" viewBox="0 0 25 25" fill="none" stroke="#222" stroke-width="1">
    <circle cx="12.5" cy="12.5" r="12"/><path d="M14.5 7.5 l-5 5 l5 5"/>
  </svg>
  <svg class="slider-arrow next" viewBox="0 0 25 25" fill="none" stroke="#222" stroke-width="1">
    <circle cx="12.5" cy="12.5" r="12"/><path d="M10.5 7.5 l5 5 l-5 5"/>
  </svg>
  <div class="partner-logo">
    <span class="partner-logo-mark"></span>
    <span class="partner-logo-name">Ledgerwick</span>
  </div>
  <p class="testimonial">Kavreo are great devlopers whise concentration on detail does not compromise the delivery of work</p>
</section>

<section class="newsletter">
  <svg class="newsletter-icon" width="30" height="24" viewBox="0 0 30 24" fill="none" stroke="#fff" stroke-width="2.4" stroke-linejoin="round">
    <rect x="1.5" y="1.5" width="27" height="21" rx="2.5"/><path d="M2 3 l13 11 l13 -11"/>
  </svg>
  <p class="newsletter-label">Join the newsletter &amp; stay informed</p>
  <form class="newsletter-form">
    <input class="newsletter-input" type="email" placeholder="Enter Email">
    <button class="newsletter-button" type="button">SUBSCRIBE</button>
  </form>
</section>

<footer class="site-footer">
  <h4 class="footer-heading links">USEFULL LINKS</h4>
  <ul class="footer-links">
    <li>HOME</li><li>ABOUT</li><li>PORTFOLIO</li><li>CONTACT</li>
  </ul>

  <h4 class="footer-heading contact">CONTACT</h4>
  <ul class="contact-list">
    <li>
      <svg width="9" height="12" viewBox="0 0 9 12"><path d="M4.5 0 a4.5 4.5 0 0 1 4.5 4.5 c0 3 -4.5 7.5 -4.5 7.5 s-4.5 -4.5 -4.5 -7.5 a4.5 4.5 0 0 1 4.5 -4.5z" fill="#fff"/><circle cx="4.5" cy="4.5" r="1.7" fill="#0d4482"/></svg>
      <span>Suite 42, Level 3|8 Wattlebrook<br>Lane|Fernvale Heights VIC 3999</span>
    </li>
    <li>
      <svg width="12" height="9" viewBox="0 0 12 9" fill="none" stroke="#fff" stroke-width="1.2"><rect x=".6" y=".6" width="10.8" height="7.8" rx="1"/><path d="M1 1.2 l5 4 l5 -4"/></svg>
      <span>support@kavreo.example</span>
    </li>
    <li>
      <svg width="11" height="11" viewBox="0 0 11 11"><path d="M2.2 0.5 l2 2.4 l-1 1.4 a6 6 0 0 0 3.5 3.5 l1.4 -1 l2.4 2 l-1.4 1.7 c-4.5 0 -8.6 -4.1 -8.6 -8.6z" fill="#fff"/></svg>
      <span>1300 648 907</span>
    </li>
  </ul>

  <h4 class="footer-heading partners-title">OUR PARTNERS</h4>
  <div class="partner-badges">
    <div class="partner-badge"><span class="partner-badge-mark"></span>Torvista</div>
    <div class="partner-badge"><span class="partner-badge-mark"></span>QRX</div>
    <div class="partner-badge"><span class="partner-badge-mark"></span>Quellcast</div>
    <div class="partner-badge"><span class="partner-badge-mark"></span>DataVane</div>
  </div>

  <p class="copyright"><strong>@ KAVREO ECOMMERCE&nbsp; 2016</strong> | All Rights Reserved</p>
</footer>

</body>
</html>
```